BOLD & MINIMALIST DESIGN NEEDED

We want a very bold but minimalistic business card design that is impactful and utilizes both sides of the business card. Our current logo is included for your use.

We want bold fonts and good use of negative space. We don't want the logo to overpower the design.

Target Market(s)

Professionals who are building new commercial buildings.

Industry/Entity Type

Construction

Contact Information for Business Card

Name, Title, email, office phone, cell phone, website

Font styles to use
Serif
Sans Serif

Requirements
Must have
• Bold design!

```html
<!DOCTYPE html>
<html lang="en">
<head>
<meta charset="utf-8">
<title>Ridgeline Design + Build – Business Card</title>
<link rel="stylesheet" href="https://fonts.googleapis.com/css2?family=Archivo:wght@800&family=Questrial&family=Roboto:wght@500&display=swap">
<style>
  :root {
    --backdrop: #262626;
    --card-dark: #1f1f20;
    --card-dark-edge: #2b2b2c;
    --card-light: #f1f1ef;
    --ink: #1c1c1e;
    --accent: #6cb52d;
    --paper-text: #ffffff;
  }
  * { margin: 0; padding: 0; box-sizing: border-box; }
  html, body {
    width: 1200px; height: 576px; overflow: hidden;
    background: var(--backdrop);
  }
  .stage { position: relative; width: 1200px; height: 576px; }

  .card {
    position: absolute; top: 139px;
    height: 293px;
    border-radius: 9px; overflow: hidden;
  }

  /* Front */
  .card--front {
    left: 102px; width: 486px;
    background: linear-gradient(135deg, var(--card-dark-edge), var(--card-dark));
  }
  .front-wordmark {
    position: absolute; left: 48px; top: 121px; width: 219px;
    font-family: "Archivo", sans-serif; font-weight: 800;
    color: var(--paper-text); text-align: center; line-height: 1;
  }
  .front-wordmark .name { display: block; font-size: 37px; letter-spacing: 0.3px; }
  .front-wordmark .tagline { display: block; font-size: 14px; letter-spacing: 4.6px; margin-top: 3px; }

  /* Back */
  .card--back {
    left: 596px; width: 480px;
    background: var(--card-light);
  }
  .back-band {
    position: absolute; left: 0; right: 0; bottom: 0; height: 88px;
    background: var(--ink);
  }
  .back-rule {
    position: absolute; left: 0; right: 0; bottom: 92px; height: 4px;
    background: var(--accent);
  }
  .back-wordmark {
    position: absolute; left: 44px; top: 119px; width: 202px;
    font-family: "Archivo", sans-serif; font-weight: 800;
    color: var(--ink); text-align: center; line-height: 1;
  }
  .back-wordmark .name { display: block; font-size: 34px; letter-spacing: 0.2px; }
  .back-wordmark .tagline { display: block; font-size: 13.5px; letter-spacing: 4.2px; margin-top: 3px; }

  .holder {
    position: absolute; right: 26px; top: 38px; text-align: right;
  }
  .holder-name {
    font-family: "Roboto", sans-serif; font-weight: 500;
    font-size: 22px; line-height: 1; color: var(--accent);
  }
  .holder-title {
    font-family: "Questrial", sans-serif;
    font-size: 12px; color: var(--ink); margin-top: 5px;
  }

  .contact-list {
    position: absolute; right: 26px; top: 214px;
    list-style: none; text-align: right;
    font-family: "Questrial", sans-serif; font-size: 12.5px;
    color: var(--paper-text);
  }
  .contact-list li {
    display: flex; align-items: center; justify-content: flex-end;
    gap: 6px; height: 17px;
  }
  .contact-list svg { width: 10px; height: 10px; fill: var(--accent); }
</style>
</head>
<body>
<main class="stage">
  <section class="card card--front" aria-label="Card front">
    <div class="front-wordmark">
      <span class="name">RIDGELINE</span>
      <span class="tagline">DESIGN + BUILD</span>
    </div>
  </section>

  <section class="card card--back" aria-label="Card back">
    <div class="back-rule"></div>
    <div class="back-band"></div>

    <div class="back-wordmark">
      <span class="name">RIDGELINE</span>
      <span class="tagline">DESIGN + BUILD</span>
    </div>

    <div class="holder">
      <p class="holder-name">Daniel Reyes</p>
      <p class="holder-title">Director</p>
    </div>

    <ul class="contact-list">
      <li>555-014-2290
        <svg viewBox="0 0 10 10" aria-hidden="true"><path d="M1 3 C1 2 2 1.5 5 1.5 C8 1.5 9 2 9 3 L9 4 L7 4 L7 3 L3 3 L3 4 L1 4 Z M2 5 L8 5 L9 9 L1 9 Z"/></svg>
      </li>
      <li>dan@ridgelinebuild.com
        <svg viewBox="0 0 10 10" aria-hidden="true"><path d="M0.5 2 L9.5 2 L5 5.5 Z M0.5 3 L5 6.5 L9.5 3 L9.5 8.5 L0.5 8.5 Z"/></svg>
      </li>
      <li>www.ridgelinebuild.com
        <svg viewBox="0 0 10 10" aria-hidden="true"><circle cx="5" cy="5" r="4.5"/><path d="M0.5 5 H9.5 M5 0.5 V9.5" stroke="var(--ink)" stroke-width="0.7"/><ellipse cx="5" cy="5" rx="2" ry="4.5" fill="none" stroke="var(--ink)" stroke-width="0.7"/></svg>
      </li>
    </ul>
  </section>
</main>
</body>
</html>
```